Business Card For Halvenmoor Financial Consulting

Hi, I would like a business card designed. Bold, modern.
Please use the same design as the logo. I have also attached the website design to see the overall theme.
Wordmark Font
Color: Hex: #01AEF7

```html
<!DOCTYPE html>
<html lang="en">
<head>
<meta charset="utf-8">
<title>Halvenmoor Financial Consulting – Business Card</title>
<link href="https://fonts.googleapis.com/css2?family=Montserrat:wght@400;500;700&display=swap" rel="stylesheet">
<style>
  :root {
    --brand-blue: #01AEF7;
    --card-black: #161616;
    --stage: #2a2a2a;
    --text-white: #f2f2f2;
    --text-soft: #d8d8d8;
  }
  * { box-sizing: border-box; margin: 0; padding: 0; }
  html, body {
    width: 1200px; height: 900px; overflow: hidden;
    background: var(--stage);
    font-family: "Montserrat", sans-serif;
  }
  .canvas {
    width: 1200px; height: 900px;
    display: flex; flex-direction: column;
    align-items: center; justify-content: center; gap: 40px;
  }
  .card {
    position: relative;
    width: 700px; height: 400px;
    background: var(--card-black);
    border-bottom: 3px solid var(--brand-blue);
    border-right: 3px solid var(--brand-blue);
    box-shadow: 0 14px 30px rgba(0,0,0,0.45);
    overflow: hidden;
  }
  /* Front */
  .wordmark {
    position: absolute; left: 56px; top: 52px;
    display: flex; align-items: center; gap: 14px;
  }
  .wordmark-square {
    width: 30px; height: 30px;
    border: 4px solid var(--brand-blue);
  }
  .wordmark-name {
    font-weight: 700; font-size: 24px; letter-spacing: 2px;
    color: var(--text-white); text-transform: uppercase;
  }
  .contact {
    position: absolute; left: 56px; top: 150px;
    color: var(--text-white); font-size: 17px; line-height: 1.5;
  }
  .address { margin-bottom: 18px; }
  .contact-list { list-style: none; }
  .contact-list li { display: flex; align-items: center; gap: 12px; }
  .contact-icon { width: 14px; height: 14px; flex: none; }
  .holder {
    position: absolute; right: 60px; top: 190px; text-align: right;
  }
  .holder-name {
    font-weight: 700; font-size: 26px; letter-spacing: 1px;
    color: var(--brand-blue); text-transform: uppercase;
  }
  .holder-title {
    font-size: 18px; color: var(--text-soft); margin-top: 4px;
  }
  .edge-tab {
    position: absolute; right: 0; top: 196px;
    width: 16px; height: 58px; background: var(--brand-blue);
  }
  /* Back */
  .card-back { display: flex; align-items: center; justify-content: center; }
  .back-mark { display: flex; align-items: center; gap: 20px; }
  .back-square {
    width: 54px; height: 54px;
    border: 7px solid var(--brand-blue);
  }
  .back-name {
    font-weight: 700; font-size: 30px; letter-spacing: 2px;
    color: var(--brand-blue); text-transform: uppercase;
  }
</style>
</head>
<body>
<main class="canvas">
  <section class="card card-front">
    <div class="wordmark">
      <span class="wordmark-square"></span>
      <span class="wordmark-name">Halvenmoor Financial Consulting</span>
    </div>
    <div class="contact">
      <p class="address">4170 Quayside Harbor<br>Brightwater CA 92711</p>
      <ul class="contact-list">
        <li>
          <svg class="contact-icon" viewBox="0 0 24 24" fill="#01AEF7"><path d="M6.6 10.8a15 15 0 0 0 6.6 6.6l2.2-2.2a1 1 0 0 1 1-.25 11.4 11.4 0 0 0 3.6.57 1 1 0 0 1 1 1V20a1 1 0 0 1-1 1A17 17 0 0 1 3 4a1 1 0 0 1 1-1h3.5a1 1 0 0 1 1 1c0 1.25.2 2.45.57 3.6a1 1 0 0 1-.25 1z"/></svg>
          555-240-6187
        </li>
        <li>
          <svg class="contact-icon" viewBox="0 0 24 24" fill="#01AEF7"><path d="M2 5h20v14H2z M2 5l10 8 10-8" stroke="#161616" stroke-width="1.5"/></svg>
          info@HalvenmoorConsulting.com
        </li>
        <li>
          <svg class="contact-icon" viewBox="0 0 24 24"><circle cx="12" cy="12" r="10" fill="#01AEF7"/><path d="M2 12h20M12 2c3 3 3 17 0 20M12 2c-3 3-3 17 0 20" stroke="#161616" stroke-width="1.5" fill="none"/></svg>
          www.HalvenmoorConsulting.com
        </li>
      </ul>
    </div>
    <div class="holder">
      <p class="holder-name">Corin Ashvale</p>
      <p class="holder-title">President</p>
    </div>
    <span class="edge-tab"></span>
  </section>

  <section class="card card-back">
    <div class="back-mark">
      <span class="back-square"></span>
      <span class="back-name">Halvenmoor</span>
    </div>
  </section>
</main>
</body>
</html>
```